We need a complete design for our construction company KELTO CONSTRUCTION based in Auckland New Zealand, we need a logo, website, business card, vehicle design etc..
We are a mid to high-end construction company who work mostly on residential projects and some commercial.

What we want to see in the design;
Professional,
Architectural,
Simple,
Alternative,

We want the design to communicate professionalism, high quality wormanship and and quality service.

Target Market(s)

People looking for a quality building/ construction company

Industry/Entity Type

Construction Company

Contact Information for Business Card

KELTO CONSTRUCTION.co.nz
Lino Verasek
lino@keltoconstruction.example.nz
021 5807 462

Logo Text

KELTO CONSTRUCTION

Number of Pages Required

5+ page

Font styles to use
Sans Serif

Colors

Designer to choose colors to be used in the design.

Requirements
Must have
• Must appear high end, professional, quality, be simple, easy to use, give security to potential clients
Nice to have
• high-quality photos of our recent projects
• about us page
• blog page
• contact us page
• high quality content
Should not have
• should not be hard to use and have too much going on.

```html
<!DOCTYPE html>
<html lang="en">
<head>
<meta charset="utf-8">
<title>KELTO CONSTRUCTION</title>
<link href="https://fonts.googleapis.com/css2?family=Oswald:wght@400;500&family=Tinos:wght@400;700&family=Josefin+Sans:wght@400;600;700&display=swap" rel="stylesheet">
<style>
:root{
  --yellow:#f7c21b;
  --dark:#2f2f2f;
  --darker:#262626;
  --ink:#222;
  --text:#555;
  --muted:#8a8a8a;
  --grey-bg:#efefef;
  --line:#d9d9d9;
  --white:#fff;
  --ghost:rgba(0,0,0,.06);
}
*{box-sizing:border-box;margin:0;padding:0}
html,body{width:1200px;height:3442px;overflow:hidden}
body{font-family:"Josefin Sans",Arial,sans-serif;color:var(--text);background:var(--white);position:relative}
.abs{position:absolute}
section,header,footer{position:absolute;left:0;width:1200px}
.serif{font-family:"Tinos","Times New Roman",serif}

/* header / hero */
.hero{top:0;height:615px;background:linear-gradient(180deg,#6a2a0a 0%,#c4581a 22%,#e08a2a 34%,#b1501a 48%,#4a1c08 70%,#1c0c05 100%)}
.brand{left:99px;top:38px;display:flex;align-items:center;gap:12px;color:var(--white);font-family:"Tinos",serif;font-size:19px;line-height:1.05;letter-spacing:.5px}
.brand .mark{width:26px;height:26px;background:var(--yellow)}
.nav{left:473px;top:70px;display:flex;gap:0;font-family:"Tinos",serif;font-size:14px;color:var(--white);letter-spacing:.3px}
.nav a{color:inherit;text-decoration:none;position:absolute;white-space:nowrap}
.nav a.active{color:var(--yellow)}
.nav a.active::after{content:"";position:absolute;left:50%;top:20px;width:7px;height:7px;border-radius:50%;background:var(--white);transform:translateX(-50%)}
.hero-title{left:100px;top:324px;color:var(--white);font-family:"Oswald",sans-serif;line-height:1.05}
.hero-title .small{font-size:40px}
.hero-title .big{font-size:58px}
.dots{left:100px;top:489px;display:flex;gap:5px}
.dots i{width:13px;height:13px;border-radius:50%;border:2px solid var(--white)}
.dots i.on{background:var(--yellow);border-color:var(--yellow)}

/* quote */
.quote{left:794px;top:553px;width:307px;height:445px;background:#f1f1f1;z-index:2}
.quote-head{height:62px;background:var(--yellow);color:var(--white);display:flex;align-items:center;justify-content:center;gap:16px;font-family:"Tinos",serif;font-size:17px;letter-spacing:.5px}
.quote .field{position:absolute;left:30px;width:237px;border-bottom:1px solid var(--line);font-size:13px;color:var(--ink);padding-bottom:14px}
.quote .submit{position:absolute;left:73px;top:374px;width:161px;height:41px;background:var(--dark);color:var(--white);font-family:"Tinos",serif;font-size:13px;letter-spacing:.8px;display:flex;align-items:center;justify-content:center}

/* about */
.about{top:615px;height:440px}
.about h1{position:absolute;left:100px;top:64px;font-family:"Tinos",serif;font-weight:400;font-size:30px;color:var(--ink);letter-spacing:.3px;z-index:1}
.about h1 span{color:var(--yellow)}
.about .ghost{position:absolute;left:470px;top:58px;font-family:"Tinos",serif;font-size:40px;color:var(--ghost)}
.about p.lead{position:absolute;left:100px;top:122px;width:660px;font-size:14px;line-height:24px;color:#444}
.proj{position:absolute;top:307px;width:330px}
.proj svg{position:absolute;left:0;top:8px}
.proj h3{position:absolute;left:61px;top:0;font-family:"Tinos",serif;font-weight:400;font-size:16px;color:var(--yellow);white-space:nowrap}
.proj p{position:absolute;left:61px;top:22px;width:270px;font-size:12px;line-height:18px;color:#555}

/* section titles */
.sec-title{position:absolute;left:0;width:1200px;text-align:center;font-family:"Tinos",serif;font-size:28px;color:var(--ink)}
.sec-title span{color:var(--yellow)}
.sec-ghost{position:absolute;left:0;width:1200px;text-align:center;font-family:"Tinos",serif;font-size:42px;color:var(--ghost);letter-spacing:1px}

/* services */
.services{top:1055px;height:609px;background:var(--grey-bg)}
.card{position:absolute;top:134px;width:312px;height:406px;background:var(--white);border-bottom:3px solid var(--yellow);box-shadow:0 1px 3px rgba(0,0,0,.08)}
.card .photo{height:188px}
.card .badge{position:absolute;left:50%;top:151px;width:74px;height:74px;margin-left:-37px;border-radius:50%;background:var(--yellow);border:5px solid var(--white);display:flex;align-items:center;justify-content:center}
.card h3{position:absolute;top:244px;width:100%;text-align:center;font-family:"Tinos",serif;font-weight:400;font-size:17px;color:var(--ink)}
.card p{position:absolute;top:276px;left:24px;right:24px;text-align:center;font-size:12.5px;line-height:21px;color:#444}
.btn-dark{position:absolute;left:50%;margin-left:-62px;top:352px;width:124px;height:35px;background:var(--dark);color:var(--white);font-family:"Tinos",serif;font-size:11px;letter-spacing:.6px;display:flex;align-items:center;justify-content:center}

/* work */
.work{top:1664px;height:626px}
.tile{position:absolute;overflow:hidden}
.tile .cap{position:absolute;left:0;right:0;bottom:0;height:34px;background:rgba(40,40,40,.55);color:var(--white);font-size:12px;letter-spacing:.4px;display:flex;align-items:center;justify-content:center}
.btn-yellow{position:absolute;left:546px;width:106px;height:33px;background:var(--yellow);color:var(--white);font-family:"Tinos",serif;font-size:11px;letter-spacing:.6px;display:flex;align-items:center;justify-content:center}

/* blog */
.blog{top:2290px;height:567px;background:var(--grey-bg)}
.feature{position:absolute;left:99px;top:133px;width:486px;height:308px}
.feature .fc{position:absolute;left:24px;bottom:18px;color:var(--white)}
.feature .fc b{display:block;font-size:13px;font-weight:600;margin-bottom:10px}
.meta{display:flex;gap:26px;font-size:12px;align-items:center}
.meta span{display:flex;align-items:center;gap:6px}
.post{position:absolute;left:615px;width:486px;height:94px}
.post .thumb{position:absolute;left:0;top:0;width:115px;height:94px}
.post h4{position:absolute;left:133px;top:4px;font-size:12.5px;font-weight:600;color:var(--ink)}
.post .meta{position:absolute;left:133px;top:28px;color:#555;gap:0;width:353px;justify-content:space-between}
.post p{position:absolute;left:133px;top:51px;width:353px;font-size:12px;line-height:19px;color:#555}
.post p b{color:var(--ink)}

/* clients */
.clients{top:2857px;height:245px}
.client{position:absolute;top:117px;width:147px;height:73px;border:1px solid #dcdcdc;display:flex;align-items:center;justify-content:center;gap:8px;font-family:"Josefin Sans",sans-serif;font-weight:700;font-size:22px;color:#222}
.client i{width:12px;height:12px;background:#222;display:block}

/* footer */
.footer{top:3102px;height:296px;background:var(--dark);color:#cfcfcf}
.footer h4{position:absolute;top:56px;font-family:"Tinos",serif;font-weight:400;font-size:15px;color:var(--white);letter-spacing:.6px}
.links{position:absolute;left:99px;top:100px;list-style:none;font-size:12.5px}
.links li{height:27.5px;display:flex;gap:14px}
.links li::before{content:"»";color:#999}
.contact{position:absolute;left:312px;top:98px;font-size:12px;line-height:17px;color:#d5d5d5}
.contact .row{display:flex;gap:12px;margin-bottom:11px}
.contact .row svg{flex:none;margin-top:1px}
.contact b{color:var(--white);font-weight:600;letter-spacing:.3px}
.map{position:absolute;left:610px;top:96px;width:235px;height:149px;border:4px solid #e3e3e3;background:linear-gradient(135deg,#e9e6df,#d8dcd3 50%,#ece8e0)}
.foot-brand{position:absolute;left:930px;top:122px;display:flex;align-items:center;gap:10px;color:var(--white);font-family:"Tinos",serif;font-size:15px;line-height:1.1}
.foot-brand .mark{width:20px;height:20px;background:var(--white)}
.social{position:absolute;left:946px;top:191px;display:flex;gap:8px}
.social i{width:27px;height:27px;border-radius:50%;display:block;background:#5a5a5a;border:2px solid #7a7a7a}
.copy{position:absolute;left:0;top:3398px;width:1200px;height:44px;background:var(--yellow);color:var(--white);font-size:12px;display:flex;align-items:center;justify-content:center}
</style>
</head>
<body>

<header class="hero" role="img" aria-label="Photo of construction workers in silhouette on a building site at sunset">
  <div class="abs brand"><span class="mark"></span><span>KELTO<br>CONSTRUCTION</span></div>
  <nav class="abs nav" style="left:0;top:70px;width:1200px">
    <a class="active" style="left:473px">HOME</a>
    <a style="left:555px">ABOUT US</a>
    <a style="left:677px">SERVICES</a>
    <a style="left:796px">OUR WORK</a>
    <a style="left:925px">BLOG</a>
    <a style="left:1005px">CONTACT US</a>
  </nav>
  <div class="abs hero-title"><div class="small">We Build</div><div class="big">Your Dreams</div></div>
  <div class="abs dots"><i class="on"></i><i></i><i></i></div>
</header>

<aside class="abs quote">
  <div class="quote-head">
    <svg width="30" height="28" viewBox="0 0 30 28" fill="none" stroke="#fff" stroke-width="2"><rect x="2" y="5" width="20" height="21"/><path d="M10 18l2-6 14-11 3 3-14 11z"/></svg>
    REQUEST A QUOTE
  </div>
  <div class="field" style="top:85px">Name</div>
  <div class="field" style="top:144px">Email</div>
  <div class="field" style="top:203px">Phone</div>
  <div class="field" style="top:262px;padding-bottom:56px">Message</div>
  <div class="submit">SUBMIT NOW</div>
</aside>

<section class="about">
  <div class="ghost">CONSTRUCTION</div>
  <h1>ABOUT <span>KELTO CONSTRUCTION</span></h1>
  <p class="lead">Lorem ipsum dolor sit amet, consectetuer adipiscing elit, sed diam nonummy nibh euismod tincidunt ut laoreet dolore magna aliquam erat volutpat. Ut wisi enim ad minim veniam, quis nostrud exerci tation ullamcorper suscipit lobortis nisl ut aliquip ex ea commodo consequat. Duis autem vel eum iriure dolor in hendrerit in vulputate velit esse molestie consequat, vel illum dolore eu feugiat nulla facilisis at vero eros et accumsan et iusto odio dignissim qui blandit praesent luptatum zzril delenit augue duis dolore te feugait nulla facilisi.</p>
  <div class="proj" style="left:99px">
    <svg width="44" height="38" viewBox="0 0 44 38" fill="#f7c21b"><path d="M22 2L2 18h6v18h28V18h6z"/><rect x="18" y="24" width="8" height="12" fill="#fff"/></svg>
    <h3>RESIDENTIAL PROJECTS</h3>
    <p>Lorem ipsum dolor sit amet, consectetuer adipiscing elit, sed diam nomy...[+]</p>
  </div>
  <div class="proj" style="left:440px">
    <svg width="48" height="46" viewBox="0 0 48 46" fill="#f7c21b"><rect x="2" y="14" width="20" height="32"/><rect x="24" y="2" width="22" height="44"/><g fill="#fff"><rect x="6" y="19" width="4" height="4"/><rect x="14" y="19" width="4" height="4"/><rect x="6" y="28" width="4" height="4"/><rect x="14" y="28" width="4" height="4"/><rect x="29" y="8" width="4" height="4"/><rect x="37" y="8" width="4" height="4"/><rect x="29" y="17" width="4" height="4"/><rect x="37" y="17" width="4" height="4"/><rect x="29" y="26" width="4" height="4"/><rect x="37" y="26" width="4" height="4"/></g></svg>
    <h3>RESIDENTIAL PROJECTS</h3>
    <p>Lorem ipsum dolor sit amet, consectetuer adipiscing elit, sed diam nomy...[+]</p>
  </div>
</section>

<section class="services">
  <div class="sec-ghost" style="top:64px">WE SPECIALIZING IN</div>
  <h2 class="sec-title" style="top:70px;font-weight:400">WE <span>SPECIALIZING IN</span></h2>

  <article class="card" style="left:99px">
    <div class="photo" role="img" aria-label="Photo of two builders in hard hats reviewing plans" style="background:linear-gradient(160deg,#d9cfc0,#b89c74 60%,#8a7458)"></div>
    <div class="badge"><svg width="30" height="30" viewBox="0 0 30 30" fill="none" stroke="#fff" stroke-width="2.2"><path d="M4 14L15 4l11 10"/><path d="M7 12v14h16V12"/><path d="M11 16l8 8M19 16l-8 8"/></svg></div>
    <h3>INTERIOR RENOVATION</h3>
    <p>Lorem ipsum dolor sit amet, consectetur adipiscing elit. Praesent vestibulum velit felis. Maecenas ac faucibus turpis.</p>
    <div class="btn-dark">READ MORE</div>
  </article>

  <article class="card" style="left:445px">
    <div class="photo" role="img" aria-label="Photo of a couple meeting with a consultant at a table" style="background:linear-gradient(160deg,#c9d2d6,#a5998a 55%,#6f655c)"></div>
    <div class="badge"><svg width="30" height="30" viewBox="0 0 30 30" fill="none" stroke="#fff" stroke-width="2.2"><rect x="4" y="6" width="18" height="20"/><path d="M12 20l3-7 10-9 2 2-9 10z"/></svg></div>
    <h3>DESIGN &amp; BUILD PACKAGE</h3>
    <p>Lorem ipsum dolor sit amet, consectetur adipiscing elit. Praesent vestibulum velit felis. Maecenas ac faucibus turpis.</p>
    <div class="btn-dark">READ MORE</div>
  </article>

  <article class="card" style="left:789px">
    <div class="photo" role="img" aria-label="Photo of two workers in overalls tiling a wall" style="background:linear-gradient(160deg,#e6e6e2,#c3c2bc 55%,#6b7a93)"></div>
    <div class="badge"><svg width="30" height="30" viewBox="0 0 30 30" fill="none" stroke="#fff" stroke-width="2.2"><rect x="4" y="4" width="16" height="8"/><path d="M20 8h4v7H12v4"/><rect x="10" y="19" width="4" height="8"/></svg></div>
    <h3>TILING AND PAINTING</h3>
    <p>Lorem ipsum dolor sit amet, consectetur adipiscing elit. Praesent vestibulum velit felis. Maecenas ac faucibus turpis.</p>
    <div class="btn-dark">READ MORE</div>
  </article>
</section>

<section class="work">
  <div class="sec-ghost" style="top:82px">OUR WORK</div>
  <h2 class="sec-title" style="top:88px;font-weight:400">OUR <span>WORK</span></h2>

  <div class="tile" style="left:99px;top:130px;width:238px;height:179px" role="img" aria-label="Photo of a building interior framed in steel studs"><div style="height:100%;background:linear-gradient(160deg,#d8d8d4,#a9a79f 60%,#7d7a73)"></div><div class="cap">LOREM IPSUM</div></div>
  <div class="tile" style="left:353px;top:130px;width:239px;height:179px" role="img" aria-label="Photo of a handshake over a site meeting"><div style="height:100%;background:linear-gradient(160deg,#5d6166,#3e4246 60%,#2b2e31)"></div><div class="cap">LOREM IPSUM</div></div>
  <div class="tile" style="left:610px;top:130px;width:237px;height:379px" role="img" aria-label="Photo of a modern high-rise building at dusk"><div style="height:100%;background:linear-gradient(180deg,#6f89a8,#3d526b 55%,#1f2b3a)"></div><div class="cap">LOREM IPSUM</div></div>
  <div class="tile" style="left:863px;top:130px;width:238px;height:179px" role="img" aria-label="Photo of a hard hat, tape measure and blueprints"><div style="height:100%;background:linear-gradient(160deg,#e8ecef,#c9d3db 55%,#d9b04a)"></div><div class="cap">LOREM IPSUM</div></div>
  <div class="tile" style="left:99px;top:328px;width:493px;height:181px" role="img" aria-label="Photo of a large two-storey family home with lawn"><div style="height:100%;background:linear-gradient(180deg,#a9c3d6,#b9bcb6 45%,#5f7a3e 80%,#46602c)"></div><div class="cap">LOREM IPSUM</div></div>
  <div class="tile" style="left:863px;top:328px;width:238px;height:181px" role="img" aria-label="Photo of builders' hands and tools on a table from above"><div style="height:100%;background:linear-gradient(160deg,#8a6a4a,#5b4632 55%,#d0a83a)"></div><div class="cap">LOREM IPSUM</div></div>

  <div class="btn-yellow" style="top:541px">VIEW ALL</div>
</section>

<section class="blog">
  <div class="sec-ghost" style="top:74px">LATEST BLOG POSTS</div>
  <h2 class="sec-title" style="top:80px;font-weight:400">LATEST <span>BLOG POSTS</span></h2>

  <div class="feature" role="img" aria-label="Photo of a glass office tower under construction with plans in the foreground" style="background:linear-gradient(160deg,#9fc0e0,#4f7fb2 50%,#2a4a73)">
    <div class="fc"><b>Lorem ipsum dolor sit amet consectetur.</b>
      <div class="meta">
        <span><svg width="14" height="14" viewBox="0 0 14 14" fill="none" stroke="#fff" stroke-width="1.4"><rect x="1" y="2" width="12" height="11"/><path d="M1 5h12M4 0v3M10 0v3"/></svg>25Mar, 2018</span>
        <span><svg width="15" height="13" viewBox="0 0 15 13" fill="none" stroke="#fff" stroke-width="1.4"><path d="M1 1h13v8H6l-3 3V9H1z"/></svg>115 Comments</span>
        <span><svg width="14" height="13" viewBox="0 0 14 13" fill="none" stroke="#fff" stroke-width="1.4"><path d="M7 12L1.5 6.5a3 3 0 014.5-4L7 3.5l1-1a3 3 0 014.5 4z"/></svg>210 Likes</span>
      </div>
    </div>
  </div>

  <div class="post" style="top:133px">
    <div class="thumb" role="img" aria-label="Photo of engineers reviewing drawings on site" style="background:linear-gradient(160deg,#d7cdbd,#9e8a6c)"></div>
    <h4>Lorem ipsum dolor sit amet consectetur.</h4>
    <div class="meta"><span><svg width="13" height="13" viewBox="0 0 14 14" fill="none" stroke="#f7c21b" stroke-width="1.5"><rect x="1" y="2" width="12" height="11"/><path d="M1 5h12"/></svg>21Mar, 2018</span><span><svg width="14" height="12" viewBox="0 0 15 13" fill="none" stroke="#f7c21b" stroke-width="1.5"><path d="M1 1h13v8H6l-3 3V9H1z"/></svg>115 Comments</span><span><svg width="13" height="12" viewBox="0 0 14 13" fill="none" stroke="#f7c21b" stroke-width="1.5"><path d="M7 12L1.5 6.5a3 3 0 014.5-4L7 3.5l1-1a3 3 0 014.5 4z"/></svg>210 Likes</span></div>
    <p>Lorem ipsum dolor sit amet, consectetuer adipiscing elit sed diam nonummy nibh euismod tincidunt ut laoreet... <b>[+]</b></p>
  </div>
  <div class="post" style="top:239px">
    <div class="thumb" role="img" aria-label="Photo of steel framing against the sky" style="background:linear-gradient(160deg,#a7b6c4,#6a5a4a)"></div>
    <h4>Lorem ipsum dolor sit amet consectetur.</h4>
    <div class="meta"><span><svg width="13" height="13" viewBox="0 0 14 14" fill="none" stroke="#f7c21b" stroke-width="1.5"><rect x="1" y="2" width="12" height="11"/><path d="M1 5h12"/></svg>19Mar, 2018</span><span><svg width="14" height="12" viewBox="0 0 15 13" fill="none" stroke="#f7c21b" stroke-width="1.5"><path d="M1 1h13v8H6l-3 3V9H1z"/></svg>115 Comments</span><span><svg width="13" height="12" viewBox="0 0 14 13" fill="none" stroke="#f7c21b" stroke-width="1.5"><path d="M7 12L1.5 6.5a3 3 0 014.5-4L7 3.5l1-1a3 3 0 014.5 4z"/></svg>210 Likes</span></div>
    <p>Lorem ipsum dolor sit amet, consectetuer adipiscing elit sed diam nonummy nibh euismod tincidunt ut laoreet... <b>[+]</b></p>
  </div>
  <div class="post" style="top:347px">
    <div class="thumb" role="img" aria-label="Photo of a builder in a hard hat at work" style="background:linear-gradient(160deg,#c8c3b8,#7b6f5f)"></div>
    <h4>Lorem ipsum dolor sit amet consectetur.</h4>
    <div class="meta"><span><svg width="13" height="13" viewBox="0 0 14 14" fill="none" stroke="#f7c21b" stroke-width="1.5"><rect x="1" y="2" width="12" height="11"/><path d="M1 5h12"/></svg>05Mar, 2018</span><span><svg width="14" height="12" viewBox="0 0 15 13" fill="none" stroke="#f7c21b" stroke-width="1.5"><path d="M1 1h13v8H6l-3 3V9H1z"/></svg>115 Comments</span><span><svg width="13" height="12" viewBox="0 0 14 13" fill="none" stroke="#f7c21b" stroke-width="1.5"><path d="M7 12L1.5 6.5a3 3 0 014.5-4L7 3.5l1-1a3 3 0 014.5 4z"/></svg>210 Likes</span></div>
    <p>Lorem ipsum dolor sit amet, consectetuer adipiscing elit sed diam nonummy nibh euismod tincidunt ut laoreet... <b>[+]</b></p>
  </div>

  <div class="btn-yellow" style="top:473px">VIEW ALL</div>
</section>

<section class="clients">
  <div class="sec-ghost" style="top:64px">OUR CLIENTS</div>
  <h2 class="sec-title" style="top:70px;font-weight:400">OUR <span>CLIENTS</span></h2>
  <div class="client" style="left:99px"><i></i>HALVERN</div>
  <div class="client" style="left:271px">northline</div>
  <div class="client" style="left:441px">Brackwell</div>
  <div class="client" style="left:613px">Corvanta</div>
  <div class="client" style="left:783px">Masoniq</div>
  <div class="client" style="left:954px"><i></i>HALVERN</div>
</section>

<footer class="footer">
  <h4 style="left:99px">QUICK LINKS</h4>
  <ul class="links">
    <li>Home</li><li>About Us</li><li>Services</li><li>Our Work</li><li>Blog</li><li>Contact Us</li>
  </ul>

  <h4 style="left:312px">CONTACT DETAILS</h4>
  <div class="contact">
    <div class="row"><svg width="14" height="18" viewBox="0 0 14 18" fill="#fff"><path d="M7 0a7 7 0 00-7 7c0 5 7 11 7 11s7-6 7-11a7 7 0 00-7-7zm0 10a3 3 0 110-6 3 3 0 010 6z"/></svg><div><b>KELTO CONSTRUCTION</b><br>123 Lorem ipsum dolor sit amet,<br>consectetuer adipiscing elit.</div></div>
    <div class="row"><svg width="15" height="15" viewBox="0 0 16 16" fill="#fff"><path d="M3 1l3 3-2 2a10 10 0 006 6l2-2 3 3-2 2C6 15 1 10 1 3z"/></svg>123-456-7890</div>
    <div class="row"><svg width="15" height="15" viewBox="0 0 16 16" fill="#fff"><rect x="1" y="5" width="14" height="9"/><rect x="4" y="1" width="8" height="5" fill="none" stroke="#fff" stroke-width="1.5"/></svg>123-456-7890</div>
    <div class="row"><svg width="15" height="14" viewBox="0 0 16 14" fill="none" stroke="#fff" stroke-width="1.5"><path d="M1 6l7-5 7 5v7H1z"/><path d="M1 6l7 4 7-4"/></svg>info@keltoconstruction.example.nz</div>
  </div>

  <h4 style="left:610px">LOCATION MAP</h4>
  <div class="map" role="img" aria-label="Street map showing the office location"></div>

  <div class="foot-brand"><span class="mark"></span><span>KELTO<br>CONSTRUCTION</span></div>
  <div class="social" aria-label="Social media links"><i></i><i></i><i></i><i></i></div>
</footer>
<div class="copy">Copyright © 2018 KELTO CONSTRUCTION. All Rights Reserved.</div>

</body>
</html>
```